Tri fold Brochure for a therapy center that specializes in divorcing families

I need to have a trifold brochure designed. The formatting is off so, I would need someone to reformat it. I would also like to make tweaks to the design and would welcome any design advice. This brochure is for a legal/therapuetic program called the Lantern Course. Here's a link to my website so you can get the feel. https://www.tidewell-harbor.example. I don't want a dark background. I would like dark colors to be accent colors. If you can make the bridge design nicer, that would be great.

Target Market(s)

attorneys, people divorcing or separating,, mediators

Industry/Entity Type

therapy and law

Font styles to use
Other font styles liked:
• Try to match it to the LC Brochure attached

Requirements
Must have
• I would like the colors to match m y website, using blues more as an accent rather than the major color. https://www.tidewell-harbor.examplehttps://www.tidewell-harbor.exampleI need to add my business logo
Nice to have
• I need to add my QR code as well and logo

```html
<!DOCTYPE html>
<html lang="en">
<head>
<meta charset="utf-8">
<title>Tidewell Harbor – Lantern Course Trifold</title>
<link rel="stylesheet" href="https://fonts.googleapis.com/css2?family=Cinzel:wght@400;500&family=Manrope:wght@400;500&display=swap">
<style>
  :root {
    --stage: #6d6a69;
    --paper: #f8f6f0;
    --paper-tint: #eef1f5;
    --navy: #16243a;
    --navy-soft: #2c3b52;
    --gold: #e2c63a;
    --gold-ink: #a6851a;
    --white: #ffffff;
  }
  * { box-sizing: border-box; margin: 0; padding: 0; }
  html, body { width: 756px; height: 1200px; overflow: hidden; background: var(--stage); }
  body { position: relative; font-family: "Manrope", sans-serif; color: var(--navy); }

  .sheet {
    position: absolute; left: 68px; width: 620px; height: 479px;
    background: var(--paper);
    box-shadow: 0 6px 18px rgba(0,0,0,.35);
    overflow: hidden;
  }
  .sheet--outside { top: 89px; }
  .sheet--inside { top: 632px; }

  .panel { position: absolute; top: 0; width: 207px; height: 479px; }
  .panel--left { left: 0; }
  .panel--middle { left: 207px; background: var(--paper-tint); }
  .panel--right { left: 413px; }

  .panel-art { position: absolute; inset: 0; width: 207px; height: 479px; }

  .heading {
    position: absolute;
    font-family: "Cinzel", serif; font-weight: 500; color: var(--navy);
    text-transform: uppercase; letter-spacing: .2px; line-height: 1.3;
  }
  .heading .accent { color: var(--gold-ink); }
  .gold-rule { position: absolute; left: 0; width: 102px; height: 0; border-top: 0.8px solid var(--gold-ink); }

  .body-copy { position: absolute; font-size: 6.3px; line-height: 11.5px; color: var(--navy-soft); }
  .justify { text-align: justify; }
  .center { text-align: center; }

  .tick-list { position: absolute; list-style: none; font-size: 6.2px; color: var(--navy-soft); }
  .tick-list li { position: relative; padding-left: 13px; }
  .tick-list li::before {
    content: ""; position: absolute; left: 0; top: 1.5px;
    width: 6px; height: 6px; border-radius: 50%; background: var(--navy);
  }
  .tick-list li::after {
    content: ""; position: absolute; left: 1.9px; top: 2.8px;
    width: 2.2px; height: 1.2px; border-left: 1px solid var(--white); border-bottom: 1px solid var(--white);
    transform: rotate(-45deg);
  }

  /* outside – left */
  .commitment-title { left: 22px; top: 20px; font-size: 12.5px; }
  .commitment-sub { left: 22px; top: 39px; font-size: 7px; line-height: 12.2px; }
  .commitment-copy { left: 22px; top: 82px; width: 163px; }
  .quote-mark { position: absolute; left: 20px; top: 116px; font-family: "Cinzel", serif; font-size: 32px; color: var(--gold-ink); line-height: 1; }
  .quote-text { position: absolute; left: 55px; top: 125px; width: 135px; font-size: 6.2px; line-height: 11.5px; color: var(--gold-ink); }
  .dotted-rule { position: absolute; left: 22px; top: 164px; width: 163px; border-top: 0.6px dotted var(--gold-ink); }
  .designed-title { left: 22px; top: 178px; font-size: 7px; line-height: 12.2px; }
  .designed-list { left: 22px; top: 210px; width: 182px; }
  .designed-list li { line-height: 13.7px; }

  /* outside – middle */
  .next-title { left: 0; width: 207px; top: 20px; text-align: center; font-size: 11.2px; line-height: 17px; }
  .next-copy { left: 18px; width: 171px; top: 57px; }
  .program-name { right: 28px; top: 338px; text-align: right; font-size: 13px; line-height: 17.5px; }
  .contact-list { position: absolute; right: 28px; top: 399px; text-align: right; font-size: 6.3px; line-height: 13.1px; color: var(--navy-soft); }
  .contact-list .label { color: var(--gold-ink); font-weight: 500; }

  /* outside – right */
  .brand-name {
    position: absolute; left: 0; width: 207px; top: 14px; text-align: center;
    font-family: "Cinzel", serif; font-size: 8.6px; line-height: 11px; color: var(--gold-ink);
    text-transform: uppercase; letter-spacing: .4px;
  }
  .bridge-title { left: 0; width: 207px; top: 350px; text-align: center; font-size: 11.5px; line-height: 17.4px; }
  .bridge-copy { left: 14px; width: 179px; top: 406px; font-size: 6.2px; line-height: 10.5px; }

  .web-band { position: absolute; left: 0; width: 186px; height: 21px; }
  .web-band svg { position: absolute; inset: 0; }
  .web-band span { position: absolute; left: 44px; top: 6px; font-size: 6.4px; color: var(--navy); letter-spacing: .1px; }
  .web-band--outside { top: 450px; }
  .web-band--inside { top: 452px; }

  /* inside – left */
  .what-title { left: 22px; top: 262px; font-size: 11px; line-height: 18px; }
  .what-rule { top: 307px; }
  .what-copy-a { left: 22px; top: 319px; width: 163px; }
  .what-copy-b { left: 22px; top: 365px; width: 163px; }
  .mission-title { position: absolute; left: 22px; top: 413px; font-family: "Cinzel", serif; font-weight: 500; font-size: 7.4px; color: var(--gold-ink); }
  .mission-copy { left: 22px; top: 430px; width: 163px; }

  /* inside – middle */
  .help-title { left: 0; width: 207px; top: 177px; text-align: center; font-size: 13.5px; }
  .help-copy { left: 21px; width: 165px; top: 203px; }
  .help-list { left: 37px; top: 259px; }
  .help-list li { line-height: 16.8px; }

  /* inside – right */
  .why-title { left: 22px; top: 261px; font-size: 11px; line-height: 18px; }
  .why-rule { top: 307px; }
  .why-copy { left: 22px; top: 317px; width: 163px; }
  .benefits-title { position: absolute; left: 22px; top: 350px; font-family: "Cinzel", serif; font-weight: 500; font-size: 7.4px; color: var(--gold-ink); }
  .benefits-list { left: 29px; top: 367px; }
  .benefits-list li { line-height: 13.5px; }
</style>
</head>
<body>

<section class="sheet sheet--outside">

  <div class="panel panel--left">
    <svg class="panel-art" viewBox="0 0 207 479" width="207" height="479">
      <defs>
        <linearGradient id="warmHug" x1="0" y1="0" x2="1" y2="1">
          <stop offset="0" stop-color="#d9b47c"/>
          <stop offset=".55" stop-color="#8a7a6a"/>
          <stop offset="1" stop-color="#4e5d6e"/>
        </linearGradient>
      </defs>
      <g role="img" aria-label="Photo of an adult family sharing a warm group hug outdoors at golden hour">
        <polygon points="0,361 104,330 207,361 207,479 0,479" fill="url(#warmHug)"/>
      </g>
    </svg>
    <h2 class="heading commitment-title">Our <span class="accent">Commitment</span></h2>
    <p class="heading commitment-sub">We believe every family deserves<br>a thoughtful transition.</p>
    <span class="gold-rule" style="top:70px"></span>
    <p class="body-copy justify commitment-copy">Our coordinated wraparound approach empowers individuals to move forward with confidence while protecting the well-being of everyone involved.</p>
    <span class="quote-mark">&#8220;</span>
    <p class="quote-text">"Supporting families through life's transitions with compassion &amp; collaboration."</p>
    <span class="dotted-rule"></span>
    <h3 class="heading designed-title">This program is designed for<br>families who:</h3>
    <ul class="tick-list designed-list">
      <li>You're going through divorce, separation, or a<br>custody dispute</li>
      <li>May need a GAL, PC, or other legal services</li>
      <li>Feel overwhelmed managing multiple professionals</li>
      <li>Experience repeated conflict or feel stuck in crisis</li>
      <li>Want a child-centered alternative to ongoing litigation</li>
      <li>Are willing to pause litigation to take a therapeutic<br>approach</li>
    </ul>
  </div>

  <div class="panel panel--middle">
    <svg class="panel-art" viewBox="0 0 207 479" width="207" height="479">
      <defs>
        <linearGradient id="clinicPhoto" x1="0" y1="0" x2="0" y2="1">
          <stop offset="0" stop-color="#a9c6e4"/>
          <stop offset=".45" stop-color="#d6dbe0"/>
          <stop offset=".75" stop-color="#4f5c66"/>
          <stop offset="1" stop-color="#5f6d4e"/>
        </linearGradient>
      </defs>
      <g role="img" aria-label="Photo of a modern glass-fronted clinic building with landscaped shrubs">
        <polygon points="0,180 207,96 207,297 0,366" fill="url(#clinicPhoto)"/>
      </g>
      <polygon points="52,100 77,114.5 77,143.5 52,158 27,143.5 27,114.5" fill="var(--gold)"/>
    </svg>
    <h2 class="heading next-title">Let's take the<br><span class="accent">Next step together</span></h2>
    <p class="body-copy center next-copy">Our collaborative approach helps ensure you have the resources, professionals, and care you need to move forward with confidence.</p>
    <h2 class="heading program-name">Tidewell<br>Harbor<br><span class="accent">Lantern Course</span></h2>
    <p class="contact-list">
      <span class="label">Phone:</span> (555) 014-2290<br>
      <span class="label">Office:</span> 48 Quayside Road, Suite #210 Port Ellery,<br>
      Bayshore 00514<br>
      <span class="label">Website:</span> www.tidewell-harbor.example<br>
      <span class="label">Email:</span> admin@tidewell-harbor.example
    </p>
  </div>

  <div class="panel panel--right">
    <svg class="panel-art" viewBox="0 0 207 479" width="207" height="479">
      <defs>
        <linearGradient id="hikePhoto" x1="0" y1="0" x2="0" y2="1">
          <stop offset="0" stop-color="#c9d3dc"/>
          <stop offset=".35" stop-color="#5f6b46"/>
          <stop offset=".7" stop-color="#4a5b72"/>
          <stop offset="1" stop-color="#7a624a"/>
        </linearGradient>
      </defs>
      <g role="img" aria-label="Photo of a multigenerational family hiking together on a forest trail">
        <polygon points="104,57 207,93 207,297 104,335 0,297 0,93" fill="url(#hikePhoto)"/>
      </g>
    </svg>
    <p class="brand-name">Tidewell<br>Harbor</p>
    <h1 class="heading bridge-title">Bridging legal &amp;<br>therapeutic <span class="accent">support</span><br><span class="accent">for families</span></h1>
    <p class="body-copy center bridge-copy">Helping families navigate separation and divorce with coordinated care, compassionate guidance, and lasting resilience.</p>
    <div class="web-band web-band--outside">
      <svg viewBox="0 0 186 21" width="186" height="21">
        <polygon points="0,0 180,0 186,10.5 180,21 0,21" fill="var(--gold)"/>
        <circle cx="32" cy="10.5" r="3" fill="var(--navy)"/>
      </svg>
      <span>WWW.TIDEWELL-HARBOR.EXAMPLE</span>
    </div>
  </div>
</section>

<section class="sheet sheet--inside">

  <div class="panel panel--left">
    <svg class="panel-art" viewBox="0 0 207 479" width="207" height="479">
      <defs>
        <linearGradient id="sessionPhoto" x1="0" y1="0" x2="1" y2="1">
          <stop offset="0" stop-color="#ece4d6"/>
          <stop offset=".6" stop-color="#b9ab98"/>
          <stop offset="1" stop-color="#4b525c"/>
        </linearGradient>
        <linearGradient id="couplePhoto" x1="0" y1="0" x2="1" y2="1">
          <stop offset="0" stop-color="#3f6a5c"/>
          <stop offset=".5" stop-color="#c8c3b6"/>
          <stop offset="1" stop-color="#d9a9a6"/>
        </linearGradient>
      </defs>
      <g role="img" aria-label="Photo of a counselor meeting with an older woman and a younger man in a bright room">
        <polygon points="0,0 207,0 207,140 104,109 0,140" fill="url(#sessionPhoto)"/>
      </g>
      <g role="img" aria-label="Photo of an older couple talking together on a sofa">
        <polygon points="103,109 170,143 170,210 103,243 36,210 36,143" fill="url(#couplePhoto)"/>
      </g>
    </svg>
    <h2 class="heading what-title">What is the <span class="accent">Lantern</span><br><span class="accent">Course?</span></h2>
    <span class="gold-rule what-rule"></span>
    <p class="body-copy justify what-copy-a">The Lantern Course bridges the gap between legal and therapeutic support for divorcing and separating families.</p>
    <p class="body-copy justify what-copy-b">We coordinate every aspect of your care, ensuring that nothing falls through the cracks while you focus on yourself and your family.</p>
    <h3 class="mission-title">OUR MISSION</h3>
    <p class="body-copy justify mission-copy">To provide compassionate, coordinated wraparound services that help families move forward with confidence, clarity, and emotional stability.</p>
  </div>

  <div class="panel panel--middle">
    <svg class="panel-art" viewBox="0 0 207 479" width="207" height="479">
      <defs>
        <linearGradient id="playPhoto" x1="0" y1="0" x2="1" y2="1">
          <stop offset="0" stop-color="#d8d2c8"/>
          <stop offset=".5" stop-color="#6b4a3a"/>
          <stop offset="1" stop-color="#8a9ab0"/>
        </linearGradient>
        <linearGradient id="groupPhoto" x1="0" y1="0" x2="1" y2="1">
          <stop offset="0" stop-color="#e6e4df"/>
          <stop offset=".5" stop-color="#5d6470"/>
          <stop offset="1" stop-color="#6e3a45"/>
        </linearGradient>
      </defs>
      <g role="img" aria-label="Photo of a laughing mother playing with her children on a sofa">
        <polygon points="0,0 207,0 207,128 104,95 0,128" fill="url(#playPhoto)"/>
      </g>
      <polygon points="103,118 126,129.5 126,152.5 103,164 80,152.5 80,129.5" fill="var(--gold)"/>
      <g role="img" aria-label="Photo of a family therapy session with parents, children and a counselor">
        <polygon points="0,350 104,394 207,350 207,479 0,479" fill="url(#groupPhoto)"/>
      </g>
    </svg>
    <h2 class="heading help-title">How <span class="accent">we help</span></h2>
    <p class="body-copy center help-copy">The Lantern Course bridges the gap between legal and therapeutic support, providing compassionate, coordinated care for individuals and families navigating separation and divorce.</p>
    <ul class="tick-list help-list">
      <li>Family-centered guidance</li>
      <li>Coordinated therapeutic support</li>
      <li>Legal collaboration</li>
      <li>Communication between professionals</li>
      <li>Individualized care planning</li>
      <li>Emotional wellness resources</li>
    </ul>
  </div>

  <div class="panel panel--right">
    <svg class="panel-art" viewBox="0 0 207 479" width="207" height="479">
      <defs>
        <linearGradient id="handsPhoto" x1="0" y1="0" x2="1" y2="1">
          <stop offset="0" stop-color="#6a4b3c"/>
          <stop offset=".5" stop-color="#a07a62"/>
          <stop offset="1" stop-color="#4e6274"/>
        </linearGradient>
        <linearGradient id="calmRoomPhoto" x1="0" y1="0" x2="0" y2="1">
          <stop offset="0" stop-color="#6f6453"/>
          <stop offset=".5" stop-color="#d8c7a6"/>
          <stop offset="1" stop-color="#9c9184"/>
        </linearGradient>
      </defs>
      <g role="img" aria-label="Close-up photo of an older hand resting on another in comfort">
        <polygon points="0,0 207,0 207,128 104,110 0,128" fill="url(#handsPhoto)"/>
      </g>
      <g role="img" aria-label="Photo of a calm candlelit meditation room with cushions and plants">
        <polygon points="103,111 170,145 170,210 103,243 36,210 36,145" fill="url(#calmRoomPhoto)"/>
      </g>
    </svg>
    <h2 class="heading why-title">Why choose <span class="accent">Lantern</span><br><span class="accent">Course?</span></h2>
    <span class="gold-rule why-rule"></span>
    <p class="body-copy justify why-copy">Instead of navigating multiple professionals on your own, Lantern creates one coordinated support system.</p>
    <h3 class="benefits-title">BENEFITS</h3>
    <ul class="tick-list benefits-list">
      <li>Reduced stress</li>
      <li>Better communication</li>
      <li>Streamlined care</li>
      <li>Professional collaboration</li>
      <li>Stronger family outcomes</li>
      <li>Peace of mind</li>
    </ul>
    <div class="web-band web-band--inside">
      <svg viewBox="0 0 186 21" width="186" height="21">
        <polygon points="0,0 180,0 186,10.5 180,21 0,21" fill="var(--gold)"/>
        <circle cx="32" cy="10.5" r="3" fill="var(--navy)"/>
      </svg>
      <span>WWW.TIDEWELL-HARBOR.EXAMPLE</span>
    </div>
  </div>
</section>

</body>
</html>
```